Business Card Design 2018 Kestrel Machining

Hello,

We need a business card design to reflect our new website we just had designed ( http://www.kestrelmachining.ca/)

We are a growing machine shop looking to grow our clientele and are hoping to update our current business card design to match our website and industry

The colours and design of our website should match to achieve what we are looking for.

I have attached a few images for reference as well as our logo and ISO 9000 needs to be apparent on the card as well

Please let me know what you have :)
Please copy marla@kestrelmachining.ca on all communication regarding this project

Thanks !!!

Industry/Entity Type

Business

Contact Information for Business Card

Company Name, employee name and title and contact details

Colors
f78f20
ffffff
00a990

Requirements
Must have
• Our logo, Iso 9000 same colours as our website http://www.kestrelmachining.ca/

```html
<!DOCTYPE html>
<html lang="en">
<head>
<meta charset="utf-8">
<title>Kestrel Machining — Business Card</title>
<link href="https://fonts.googleapis.com/css2?family=Roboto:wght@300;400;700;900&display=swap" rel="stylesheet">
<style>
  :root {
    --page: #e9e6e1;
    --card: #ffffff;
    --teal: #35b8c3;
    --teal-deep: #1f9aa6;
    --ink: #1a1a1a;
    --grey: #6a6a6a;
    --rule: #b9b9b9;
    --badge-dark: #2a2a2a;
    --badge-blue: #2b3d8c;
  }
  * { box-sizing: border-box; margin: 0; padding: 0; }
  html, body { width: 1200px; height: 886px; overflow: hidden; }
  body {
    background: var(--page);
    font-family: "Roboto", Arial, sans-serif;
    display: flex;
    align-items: center;
    justify-content: center;
    gap: 40px;
  }
  .card {
    position: relative;
    width: 540px;
    height: 310px;
    background: var(--card);
    box-shadow: 0 6px 18px rgba(0,0,0,.18);
    overflow: hidden;
  }

  /* Front */
  .arm-artwork {
    position: absolute;
    top: 26px;
    right: 34px;
    width: 250px;
    height: 230px;
    border-radius: 24px;
    background: linear-gradient(145deg, var(--teal) 0%, var(--teal-deep) 100%);
    opacity: .9;
  }
  .identity { position: absolute; left: 34px; top: 52px; }
  .person-name {
    color: var(--teal);
    font-weight: 700;
    font-size: 24px;
    letter-spacing: .5px;
    text-transform: uppercase;
  }
  .person-title {
    color: var(--grey);
    font-weight: 300;
    font-size: 13px;
    margin-top: 2px;
    text-transform: uppercase;
  }
  .dotted-rule {
    width: 200px;
    border-top: 1px dotted var(--rule);
    margin: 12px 0;
  }
  .contact-row {
    display: flex;
    align-items: center;
    gap: 10px;
    font-size: 12px;
    font-weight: 300;
    color: var(--ink);
    line-height: 18px;
  }
  .contact-row svg { width: 11px; height: 11px; flex: none; fill: var(--teal); }
  .address-row { align-items: flex-start; }
  .address-row svg { margin-top: 3px; }

  /* Back */
  .back { display: flex; align-items: center; justify-content: center; }
  .brand {
    display: flex;
    align-items: center;
    gap: 12px;
    margin-top: -30px;
  }
  .brand-square { width: 30px; height: 30px; background: var(--teal); }
  .brand-name {
    font-weight: 900;
    font-size: 30px;
    color: var(--ink);
    text-transform: uppercase;
    letter-spacing: 1px;
  }
  .back-web {
    position: absolute;
    left: 0; right: 0;
    bottom: 86px;
    text-align: center;
    font-size: 11px;
    font-weight: 300;
    letter-spacing: 4px;
    color: var(--grey);
  }
  .badges {
    position: absolute;
    right: 34px;
    bottom: 26px;
    display: flex;
    gap: 12px;
    align-items: center;
  }
  .badge-iso { width: 62px; height: 26px; border: 2px solid var(--badge-dark); border-radius: 4px; }
  .badge-partner { width: 58px; height: 24px; background: var(--badge-blue); }
</style>
</head>
<body>

  <section class="card front">
    <div class="arm-artwork" role="img" aria-label="Teal robotic arm illustration"></div>
    <div class="identity">
      <h1 class="person-name">Dana Whitlock</h1>
      <p class="person-title">CEO/Founder</p>
      <div class="dotted-rule"></div>
      <div class="contact-row address-row">
        <svg viewBox="0 0 10 10"><path d="M5 0a3.5 3.5 0 0 0-3.5 3.5C1.5 6 5 10 5 10s3.5-4 3.5-6.5A3.5 3.5 0 0 0 5 0zm0 5a1.5 1.5 0 1 1 0-3 1.5 1.5 0 0 1 0 3z"/></svg>
        <span>412 Foundry Road<br>Hamilton, Ontario L8N 2T4</span>
      </div>
      <div class="dotted-rule"></div>
      <div class="contact-row">
        <svg viewBox="0 0 10 10"><path d="M2 0l2 2.5-1 1.2a6 6 0 0 0 3.3 3.3l1.2-1L10 8l-1 2C4 10 0 6 0 1z"/></svg>
        <span>555 210 4471</span>
      </div>
      <div class="contact-row">
        <svg viewBox="0 0 10 10"><path d="M2.5 0h5v10h-5zM3.5 1v7h3V1z"/></svg>
        <span>555 382 6610</span>
      </div>
      <div class="contact-row">
        <svg viewBox="0 0 10 10"><path d="M2 0h6v3H2zM0 3.5h10V8H8v2H2V8H0z"/></svg>
        <span>555 734 0925</span>
      </div>
      <div class="contact-row">
        <svg viewBox="0 0 10 10"><path d="M0 2h10v6H0zM1 3l4 3 4-3v-.2H1z"/></svg>
        <span>marla@kestrelmachining.ca</span>
      </div>
      <div class="contact-row">
        <svg viewBox="0 0 10 10"><circle cx="5" cy="5" r="5"/></svg>
        <span>www.kestrelmachining.ca</span>
      </div>
    </div>
  </section>

  <section class="card back">
    <div class="brand">
      <span class="brand-square"></span>
      <span class="brand-name">Kestrel Machining</span>
    </div>
    <p class="back-web">www.kestrelmachining.ca</p>
    <div class="badges">
      <div class="badge-iso" role="img" aria-label="Quality certification badge"></div>
      <div class="badge-partner" role="img" aria-label="Partner certification badge"></div>
    </div>
  </section>

</body>
</html>
```